Business Card for Vorla Parts Wholesale supplier

Hi There! I need a new business card for our company. We are specialized in selling Vorla parts, mostly we sell new LCD screens for Zelnar and Drelks. I would like to see that back in the design.

You can find the colors and logo's on our website: www.hartuvo.nl

Industry/Entity Type

Business

Contact Information for Business Card

My Details:
Tobias Lindqvist

Phone: 0031687203316
E-mail: Tobias@hartuvo.nl

Slogan: "Because Quality Matters"

Font styles to use
Sans Serif

Colors

Designer to choose colors to be used in the design.

Requirements
Must have
• A Black backside with the Hartuvo logo on it. The front side should be clean with only my contact details.
• But I'm also open for something really different or awesome!
Nice to have
• Remember that we are in the parts & repairing industry, So i'll be handing those business cards mainly to repair companies. Maybe you can do something with that thought :)

```html
<!DOCTYPE html>
<html lang="en">
<head>
<meta charset="utf-8">
<title>Hartuvo business card</title>
<link href="https://fonts.googleapis.com/css2?family=Roboto:wght@400;500&display=swap" rel="stylesheet">
<style>
  :root {
    --page: #e4e4e4;
    --card: #141516;
    --card-back: #1e1e1f;
    --orange: #ec6f24;
    --white: #ffffff;
    --muted: #d9d9d9;
  }
  * { box-sizing: border-box; margin: 0; padding: 0; }
  html, body {
    width: 1200px; height: 576px; overflow: hidden;
    background: var(--page);
    font-family: "Roboto", Arial, sans-serif;
  }
  .card {
    position: absolute; top: 138px;
    width: 484px; height: 294px;
    border-radius: 14px; overflow: hidden;
  }
  .card--back { left: 82px; background: var(--card-back); }
  .card--front { left: 602px; background: var(--card); }

  .back-photo {
    position: absolute; inset: 0;
    background:
      radial-gradient(ellipse at 62% 18%, #3a3a3b 0%, transparent 45%),
      linear-gradient(160deg, #232324 0%, #2b2b2c 45%, #1c1c1d 70%, #222223 100%);
  }
  .brand {
    position: absolute; display: flex; align-items: center;
    color: var(--white); font-weight: 500; letter-spacing: 0.5px;
  }
  .brand__dot { border-radius: 50%; background: var(--orange); flex: none; }
  .brand--large { left: 104px; top: 120px; gap: 14px; font-size: 50px; }
  .brand--large .brand__dot { width: 46px; height: 46px; }
  .brand--small { left: 16px; top: 32px; gap: 10px; font-size: 38px; }
  .brand--small .brand__dot { width: 34px; height: 34px; }

  .front-accent {
    position: absolute; left: 238px; top: -30px;
    width: 360px; height: 360px; border-radius: 50%;
    background: var(--orange);
  }
  .person { position: absolute; left: 24px; top: 166px; }
  .person__name { color: var(--orange); font-size: 18px; font-weight: 500; }
  .person__role { color: var(--muted); font-size: 11px; margin-top: 3px; }

  .contact { position: absolute; left: 24px; top: 224px; list-style: none; }
  .contact__item {
    display: flex; align-items: center; gap: 12px;
    height: 17px; color: var(--muted); font-size: 11.5px;
  }
  .contact__icon { width: 11px; height: 11px; fill: var(--orange); flex: none; }
</style>
</head>
<body>
  <section class="card card--back">
    <div class="back-photo" role="img" aria-label="Dark close-up photo of a smartphone with a cracked screen"></div>
    <div class="brand brand--large"><span class="brand__dot"></span>hartuvo</div>
  </section>

  <section class="card card--front">
    <div class="front-accent"></div>
    <div class="brand brand--small"><span class="brand__dot"></span>hartuvo</div>
    <div class="person">
      <p class="person__name">Tobias Lindqvist</p>
      <p class="person__role">Managing Director</p>
    </div>
    <ul class="contact">
      <li class="contact__item">
        <svg class="contact__icon" viewBox="0 0 12 12"><path d="M1 3.5C1 2 3 1 6 1s5 1 5 2.5V5H8.5V4h-5v1H1z"/><rect x="2" y="6" width="8" height="5" rx="1"/></svg>
        0031687203316
      </li>
      <li class="contact__item">
        <svg class="contact__icon" viewBox="0 0 12 12"><path d="M6 0.5a5.5 5.5 0 1 0 0 11a5.5 5.5 0 1 0 0-11zm0 1.2c.7.8 1.2 2.2 1.3 3.7H4.7C4.8 3.9 5.3 2.5 6 1.7zM1.8 6.6h1.7c.1 1.3.4 2.4.9 3.2A4.4 4.4 0 0 1 1.8 6.6zm0-1.2A4.4 4.4 0 0 1 4.4 2.2c-.5.8-.8 1.9-.9 3.2zm4.2 4.9c-.7-.8-1.2-2.2-1.3-3.7h2.6c-.1 1.5-.6 2.9-1.3 3.7zm1.6-.5c.5-.8.8-1.9.9-3.2h1.7a4.4 4.4 0 0 1-2.6 3.2zm.9-4.4c-.1-1.3-.4-2.4-.9-3.2a4.4 4.4 0 0 1 2.6 3.2z"/></svg>
        Tobias@hartuvo.nl
      </li>
      <li class="contact__item">
        <svg class="contact__icon" viewBox="0 0 12 12"><path d="M0.5 2.5h11v7h-11z M1.5 3.2L6 6.6l4.5-3.4" fill="none" stroke="#ec6f24" stroke-width="1.2"/><path d="M0.5 2.5h11L6 6.7z"/></svg>
        www.hartuvo.nl
      </li>
    </ul>
  </section>
</body>
</html>
```